Business Card Design Project

I need a business card designed from scratch. I have an existing logo that I can upload in Illustrator for modification or redesign.

The Company is called Query Lanterns http://querylanterns.com.au and we provide Search Engine Optimization services to Australian businesses. The current logo signifies an increase in visitors, profits etc...

There are no restrictions as to the redesign - colours, style etc are all open to change.

Cards will be full colour and one sided printed at http://www.cardmoxel.com.au so check their requirements for file format and sizes etc.

I will expect all original files upon completion of project.

Target Market(s)

Any business with a web site looking to improve their search engine rankings

Industry/Entity Type

Business

Requirements
Must have
• I like modern, sleek designs. Clean, not fussy, uncluttered.

```html
<!DOCTYPE html>
<html lang="en">
<head>
<meta charset="utf-8">
<title>Query Lanterns – Business Card</title>
<link rel="stylesheet" href="https://fonts.googleapis.com/css2?family=Source+Sans+3:wght@400;600;700;800&display=swap">
<style>
  :root {
    --stage: #4a2c18;
    --paper: #ffffff;
    --brand-blue: #1f6fb8;
    --brand-yellow: #f6c21c;
    --band-yellow: #f8c91e;
    --band-yellow-deep: #f3b712;
    --navy-light: #2d6fb4;
    --navy: #1b4a80;
    --navy-deep: #163a66;
    --ink: #333333;
    --ink-soft: #444444;
  }
  * { box-sizing: border-box; margin: 0; padding: 0; }
  html, body { width: 1200px; height: 412px; overflow: hidden; }
  body {
    background: var(--stage);
    font-family: "Source Sans 3", "Myriad Pro", Arial, sans-serif;
    position: relative;
  }
  .card {
    position: absolute;
    top: 64px;
    width: 498px;
    height: 284px;
    background: var(--paper);
    overflow: hidden;
  }
  .card--front { left: 72px; }
  .card--back { left: 631px; }

  .brand {
    position: absolute;
    display: flex;
    align-items: center;
    gap: 10px;
    color: var(--brand-blue);
    font-weight: 800;
    white-space: nowrap;
  }
  .brand__dot {
    border-radius: 50%;
    background: var(--brand-yellow);
    flex: none;
  }
  .card--front .brand { left: 0; right: 0; top: 66px; justify-content: center; font-size: 38px; line-height: 1; }
  .card--front .brand__dot { width: 18px; height: 18px; }

  .name-band {
    position: absolute;
    left: 0; right: 0; top: 164px; height: 27px;
    background: linear-gradient(180deg, var(--band-yellow) 0%, var(--band-yellow-deep) 100%);
    text-align: center;
    font-size: 17px;
    line-height: 27px;
    color: var(--ink);
  }
  .name-band__name { font-weight: 700; }
  .name-band__title { font-weight: 400; font-size: 15px; }

  .contact-panel {
    position: absolute;
    left: 0; right: 0; top: 195px; bottom: 0;
    background: radial-gradient(ellipse 70% 120% at 45% 50%, var(--navy-light) 0%, var(--navy) 55%, var(--navy-deep) 100%);
    color: #ffffff;
    font-size: 12.5px;
  }
  .address {
    position: absolute;
    right: 290px; top: 30px;
    text-align: right;
    font-style: normal;
    line-height: 17px;
  }
  .divider {
    position: absolute;
    left: 232px; top: 20px;
    width: 1px; height: 52px;
    background: rgba(255,255,255,0.75);
  }
  .contact-list {
    position: absolute;
    left: 262px; top: 20px;
    list-style: none;
    line-height: 17px;
  }
  .contact-list li { display: flex; align-items: center; gap: 5px; }
  .contact-list svg { width: 9px; height: 9px; fill: #ffffff; flex: none; }

  .card--back .brand { left: 0; right: 0; top: 100px; justify-content: center; font-size: 42px; line-height: 1; }
  .card--back .brand__dot { width: 22px; height: 22px; }
  .web {
    position: absolute;
    left: 0; right: 0; top: 228px;
    text-align: center;
    font-size: 12px;
    font-weight: 700;
    letter-spacing: 4.2px;
    color: var(--ink-soft);
  }
</style>
</head>
<body>
  <section class="card card--front">
    <div class="brand"><span class="brand__dot"></span>Query Lanterns</div>
    <div class="name-band"><span class="name-band__name">Your Name</span> <span class="name-band__title">/ Title</span></div>
    <div class="contact-panel">
      <address class="address">Complex name,Street name<br>City, State, zip code</address>
      <div class="divider"></div>
      <ul class="contact-list">
        <li><svg viewBox="0 0 10 10" aria-hidden="true"><path d="M2 0.5 L3.6 2.6 L2.8 3.6 Q4 6 6.4 7.2 L7.4 6.4 L9.5 8 L8.2 9.6 Q3.5 9 0.4 1.8 Z"/></svg>098 765 4321</li>
        <li><svg viewBox="0 0 10 10" aria-hidden="true"><path d="M2.5 0 H7.5 V10 H2.5 Z M3.5 1.2 V6.8 H6.5 V1.2 Z"/></svg>098 765 4321</li>
        <li><svg viewBox="0 0 10 10" aria-hidden="true"><path d="M0.5 2 H9.5 V8.5 H0.5 Z M1.2 2.6 L5 5.6 L8.8 2.6 Z" fill-rule="evenodd"/></svg>enquiry@querylanterns.com.au</li>
      </ul>
    </div>
  </section>

  <section class="card card--back">
    <div class="brand"><span class="brand__dot"></span>Query Lanterns</div>
    <p class="web">www.querylanterns.com.au</p>
  </section>
</body>
</html>
```